Stationery and Business Card Design

We need stationary design for our new company lanternfold. Lanternfold is a company that provides city apartment rentals for tourists in Athens We need business cards, letterheads for A4 and A5 and envelopes for A4 A5. The design needs to be modern, friendly and corporate.

Target Market(s)

City Tourists

Industry/Entity Type

Tourism

```html
<!DOCTYPE html>
<html lang="en">
<head>
<meta charset="utf-8">
<title>Lanternfold Stationery</title>
<link href="https://fonts.googleapis.com/css2?family=Raleway:wght@400&family=Questrial&display=swap" rel="stylesheet">
<style>
  :root {
    --plum: #7b1d50;
    --plum-soft: #86305e;
    --paper: #f4f4f4;
    --paper-mark: #ebebeb;
    --ink: #555;
    --backdrop: #d3d2d4;
  }
  html, body { margin: 0; padding: 0; }
  body {
    width: 1200px; height: 991px; overflow: hidden;
    background: var(--backdrop);
    position: relative;
    font-family: "Questrial", sans-serif;
  }
  .sheet { position: absolute; background: var(--paper); box-sizing: border-box; }
  .sheet.has-band { border-top: 4px solid var(--plum); }
  .dark { background: var(--plum); }

  .brand { position: absolute; display: flex; flex-direction: column; align-items: center; transform: translateX(-50%); white-space: nowrap; }
  .brand-square { background: var(--plum); }
  .dark .brand-square { background: #fff; }
  .brand-name { font-family: "Raleway", sans-serif; font-weight: 400; color: var(--plum); line-height: 1; }
  .dark .brand-name { color: #fff; }

  .faint-square { position: absolute; background: var(--paper-mark); }
  .dark .faint-square { background: var(--plum-soft); }

  .small-print { position: absolute; color: var(--ink); white-space: nowrap; }
  .dark .small-print { color: #fff; }
  .centred { transform: translateX(-50%); text-align: center; }
  .rule { position: absolute; height: 1px; background: #999; }
  .spine { position: absolute; top: 0; bottom: 0; left: 26px; width: 1px; background: #6a1644; }
  .flap { position: absolute; left: 0; top: 0; }
</style>
</head>
<body>

  <!-- A4 letterhead -->
  <section class="sheet has-band letterhead" style="left:71px; top:104px; width:397px; height:560px;">
    <div class="brand" style="left:50%; top:33px;">
      <div class="brand-square" style="width:30px; height:30px;"></div>
      <div class="brand-name" style="font-size:21px; margin-top:6px;">Lanternfold</div>
    </div>
    <div class="faint-square" style="left:73px; top:197px; width:253px; height:253px;"></div>
    <div class="rule" style="left:37px; right:37px; top:507px;"></div>
    <div class="small-print centred" style="left:50%; top:513px; font-size:5.5px;">48 Ermou Street, Athens 105 63 · T: +30 210 555 0142 · F: +30 210 555 0143 · www.lanternfold.com</div>
  </section>

  <!-- Presentation folder -->
  <section class="sheet dark folder" style="left:507px; top:90px; width:432px; height:575px; border-radius:3px;">
    <div class="spine"></div>
    <div class="brand" style="left:216px; top:76px;">
      <div class="brand-square" style="width:42px; height:39px;"></div>
      <div class="brand-name" style="font-size:28px; margin-top:6px;">Lanternfold</div>
    </div>
    <div class="faint-square" style="left:79px; top:212px; width:276px; height:260px;"></div>
    <div class="small-print centred" style="left:50%; top:530px; font-size:7px;">www.lanternfold.com</div>
  </section>

  <!-- Business card, front -->
  <section class="sheet has-band card" style="left:66px; top:696px; width:170px; height:94px;">
    <div class="brand" style="left:50%; top:19px;">
      <div class="brand-square" style="width:18px; height:18px;"></div>
      <div class="brand-name" style="font-size:13px; margin-top:4px;">Lanternfold</div>
    </div>
    <div class="small-print centred" style="left:50%; top:65px; font-size:3.6px; line-height:1.4;">48 Ermou Street, Athens 105 63<br>T: +30 210 555 0142 · F: +30 210 555 0143 · www.lanternfold.com</div>
  </section>

  <!-- Business card, back -->
  <section class="sheet dark card" style="left:66px; top:810px; width:170px; height:94px;">
    <div class="brand" style="left:50%; top:28px;">
      <div class="brand-square" style="width:18px; height:18px;"></div>
      <div class="brand-name" style="font-size:13px; margin-top:4px;">Lanternfold</div>
    </div>
  </section>

  <!-- Compliment slip -->
  <section class="sheet has-band comp-slip" style="left:266px; top:696px; width:415px; height:208px;">
    <div class="brand" style="left:72px; top:22px;">
      <div class="brand-square" style="width:29px; height:29px;"></div>
      <div class="brand-name" style="font-size:19px; margin-top:6px;">Lanternfold</div>
    </div>
    <div class="faint-square" style="left:227px; top:20px; width:163px; height:163px;"></div>
    <div class="small-print centred" style="left:72px; top:175px; font-size:5.5px; line-height:1.4;">48 Ermou Street<br>Athens 105 63</div>
  </section>

  <!-- DL envelope, back -->
  <section class="sheet envelope-back" style="left:718px; top:696px; width:415px; height:208px;">
    <svg class="flap" width="415" height="60" viewBox="0 0 415 60" aria-hidden="true">
      <path d="M0 0 H415 L401 58 H14 Z" fill="var(--plum)"/>
    </svg>
    <div class="brand-square" style="position:absolute; left:195px; top:17px; width:26px; height:24px; background:#fff;"></div>
    <div class="small-print centred" style="left:50%; top:180px; font-size:5.5px;">www.lanternfold.com</div>
  </section>

</body>
</html>
```